New Mechanical Maintenance business needs website

New Mechanical Maintenance business in Perth Western Australia needs a nice and easy to navigate website. Showing what we do and how we can be the right fit for other small to medium size business by offering personalized service from our highly skilled team. We deal with both fixed plant repairs like food and chemical processing facilities to heavy equipment like drill rigs, Large boats and earthmoving equipment.

Target Market(s)

Small to medium business to offer personalized services/packages

Industry/Entity Type

e deal with both fixed plant repairs like food and chemical processing facilities to heavy equipment like drill rigs, Large boats and earthmoving equipment.

Coding

Coded - Design and coding required

Number of Pages Required

4 page

Font styles to use
Serif

Colors
0054AA
0677BA
7BADD7
CADEEF
E8F1F8

Requirements
Must have
• A website that is easy to navigate but covers off on the range of services/maintenance we can provide

```html
<!DOCTYPE html>
<html lang="en">
<head>
<meta charset="utf-8">
<title>Keelbrook Maintenance</title>
<link href="https://fonts.googleapis.com/css2?family=Lato:wght@400;700;900&family=Open+Sans:wght@400;600;700&display=swap" rel="stylesheet">
<style>
:root{
  --blue-deep:#0054AA;
  --blue:#0677BA;
  --blue-soft:#7BADD7;
  --blue-pale:#CADEEF;
  --blue-mist:#E8F1F8;
  --ink:#1f2a36;
  --slate:#5a5f68;
  --slate-dark:#4b5058;
  --grey-text:#6b7280;
  --black:#0b0b0c;
  --white:#ffffff;
}
*{box-sizing:border-box;margin:0;padding:0}
html,body{width:1200px;height:4804px;overflow:hidden}
body{position:relative;font-family:"Open Sans",Arial,sans-serif;color:var(--ink);background:var(--white)}
.heading{font-family:"Lato",Arial,sans-serif;font-weight:900;letter-spacing:-0.5px}
.accent{color:var(--blue)}
.btn{position:absolute;display:flex;align-items:center;justify-content:center;gap:8px;background:var(--blue-deep);color:var(--white);font-weight:700;font-size:14px;border-radius:24px;text-transform:uppercase;text-decoration:none}
.photo{position:absolute}

/* header */
.site-header{position:absolute;left:0;top:0;width:1200px;height:103px;background:var(--white)}
.brand-badge{position:absolute;left:130px;top:0;width:160px;height:128px;background:var(--white);clip-path:polygon(0 0,100% 0,100% 78%,82% 100%,18% 100%,0 78%);z-index:3;display:flex;align-items:center;justify-content:center;gap:6px}
.brand-dot{width:14px;height:14px;border-radius:50%;background:var(--blue-deep)}
.brand-name{font-family:"Lato",sans-serif;font-weight:700;font-size:15px;color:var(--ink);line-height:1.1}
.follow{position:absolute;left:622px;top:18px;display:flex;align-items:center;gap:6px;font-size:11px;font-weight:700}
.social{width:26px;height:26px;border:1.5px solid var(--ink);border-radius:50%}
.call{position:absolute;left:880px;top:12px;display:flex;gap:12px;align-items:center}
.call small{display:block;font-size:10px}
.call strong{font-size:18px;font-weight:600;white-space:nowrap}
.nav{position:absolute;top:70px;left:380px;display:flex}
.nav a{font-size:13px;font-weight:700;color:var(--ink);text-decoration:none;padding:0 0 6px}
.nav a.active{color:var(--blue-deep);border-bottom:2px solid var(--blue-deep)}

/* hero */
.hero{position:absolute;left:0;top:103px;width:1200px;height:591px;background:linear-gradient(100deg,#2a2f36 0%,#4a4038 40%,#a86a2c 75%,#e0a050 100%)}
.hero h1{position:absolute;left:145px;top:180px;font-size:46px;color:var(--white)}
.hero h1 .accent{color:var(--blue-soft)}
.hero p{position:absolute;left:145px;top:252px;width:470px;font-size:15px;font-weight:600;color:var(--white);line-height:1.6}

/* about */
.about{position:absolute;left:0;top:694px;width:1200px;height:646px;background:var(--slate)}
.about h2{position:absolute;left:215px;top:128px;font-size:36px;color:var(--white)}
.about h2 .accent{color:var(--blue-soft)}
.about-copy{position:absolute;left:600px;top:52px;width:448px;color:var(--white);font-size:12.5px;line-height:1.9;text-align:justify}
.about-copy p+p{margin-top:10px}
.stat{position:absolute;top:300px;display:flex;gap:18px;align-items:center;color:var(--white)}
.stat-icon{width:48px;height:48px;border-radius:50%;background:var(--blue-deep);position:relative}
.stat-icon::after{content:"";position:absolute;left:18px;top:8px;width:26px;height:32px;border:2px solid var(--white);background:var(--slate)}
.stat b{display:block;font-family:"Lato",sans-serif;font-size:28px;font-weight:900}
.stat span{font-size:14px}

/* services */
.section-title{position:absolute;left:0;width:1200px;text-align:center;font-size:38px;color:var(--ink)}
.lead{position:absolute;left:210px;width:780px;text-align:center;font-size:13px;line-height:1.9;color:#4a4f57}
.card{position:absolute;top:1890px;width:288px;height:365px;background:var(--white);box-shadow:0 4px 16px rgba(0,0,0,.12);text-align:center}
.card .photo{left:0;top:0;width:100%;height:210px}
.card .icon-disc{position:absolute;left:120px;top:183px;width:50px;height:50px;border-radius:50%;background:var(--blue-deep);border:3px solid var(--white)}
.card .icon-disc::after{content:"";position:absolute;left:14px;top:13px;width:16px;height:18px;border:3px solid var(--white);border-radius:3px}
.card h3{position:absolute;top:240px;width:100%;font-size:16px;font-weight:700}
.card p{position:absolute;top:268px;left:20px;right:20px;font-size:12.5px;line-height:1.8;color:var(--grey-text)}
.card .more{position:absolute;top:325px;width:100%;font-size:12px;font-weight:700;color:var(--blue-deep)}
.card.featured{background:var(--blue);color:var(--white)}
.card.featured p,.card.featured .more{color:var(--white)}
.card.featured .icon-disc{background:var(--white);border-color:var(--blue)}
.card.featured .icon-disc::after{border-color:var(--blue-deep)}
.dot-grid{position:absolute;left:455px;top:2265px;width:290px;height:40px;background-image:radial-gradient(var(--blue-pale) 1.5px,transparent 1.5px);background-size:10px 10px}

/* projects */
.projects{position:absolute;left:0;top:2470px;width:1200px;height:735px;background:linear-gradient(135deg,#0a5fae 0%,var(--blue) 50%,#0a5aa8 100%)}
.projects h2{position:absolute;left:195px;top:88px;font-size:36px;color:var(--white)}
.projects .lead-right{position:absolute;left:617px;top:95px;width:440px;color:var(--white);font-size:13px;line-height:1.9}
.pager{position:absolute;left:578px;top:652px;display:flex;gap:6px}
.pager i{width:10px;height:10px;border-radius:50%;background:var(--white)}
.pager i.on{background:transparent;border:1.5px solid var(--white)}

/* blog */
.post{position:absolute;top:3425px;width:284px;height:335px;background:var(--white);box-shadow:0 4px 16px rgba(0,0,0,.12)}
.post .photo{left:0;top:0;width:100%;height:167px}
.post h3{position:absolute;left:20px;right:16px;top:182px;font-size:15px;font-weight:600;line-height:1.35}
.post .date{position:absolute;left:20px;top:232px;font-size:12.5px;color:var(--grey-text);display:flex;gap:8px;align-items:center}
.post .date::before{content:"";width:11px;height:11px;border:1.5px solid currentColor;border-radius:2px}
.post p{position:absolute;left:20px;right:16px;top:270px;font-size:12.5px;line-height:1.8;color:var(--grey-text)}
.arrow{position:absolute;top:3570px;width:20px;height:28px}

/* contact */
.contact{position:absolute;left:0;top:3855px;width:1200px;height:615px;background:var(--slate-dark)}
.contact h2{position:absolute;left:0;width:1200px;text-align:center;top:95px;font-size:36px;color:var(--white)}
.contact h2 .accent{color:var(--blue-soft)}
.info{position:absolute;top:205px;display:flex;gap:14px;color:var(--white)}
.info b{display:block;font-size:14px;font-weight:700}
.info span{font-size:12.5px;line-height:1.4}
.field{position:absolute;left:185px;width:402px;height:45px;background:var(--white);border-radius:3px;font-size:12px;color:#8a8f96;padding:14px 18px}
.field.message{left:610px;width:405px;height:172px}

/* footer */
.site-footer{position:absolute;left:0;top:4470px;width:1200px;height:334px;background:var(--black);color:var(--white)}
.footer-brand{position:absolute;left:190px;top:55px;width:160px;height:110px;display:flex;align-items:center;gap:8px}
.footer-brand .brand-dot{background:var(--blue-soft)}
.footer-brand .brand-name{color:var(--white)}
.footer-follow{position:absolute;left:145px;top:192px;display:flex;align-items:center;gap:6px;font-size:11px;font-weight:700}
.footer-follow .social{border-color:var(--white)}
.col{position:absolute;top:70px}
.col h4{font-family:"Lato",sans-serif;font-size:17px;font-weight:700;margin-bottom:18px}
.col li{list-style:none;font-size:11.5px;line-height:24px}
.copyright{position:absolute;left:0;width:1200px;top:290px;text-align:center;font-size:11.5px}
</style>
</head>
<body>

<header class="site-header">
  <div class="brand-badge"><span class="brand-dot"></span><span class="brand-name">Keelbrook<br>Maintenance</span></div>
  <div class="follow">FOLLOW US: <span class="social"></span><span class="social"></span><span class="social"></span><span class="social"></span></div>
  <div class="call">
    <svg width="26" height="26" viewBox="0 0 24 24" fill="none" stroke="#0054AA" stroke-width="1.6"><path d="M5 3h4l2 5-3 2a12 12 0 0 0 6 6l2-3 5 2v4a2 2 0 0 1-2 2A17 17 0 0 1 3 5a2 2 0 0 1 2-2z"/></svg>
    <div><small>Call Us Today</small><strong>+61 8 5550 1472</strong></div>
  </div>
  <nav class="nav">
    <a class="active" href="#" style="margin-right:64px">HOME</a>
    <a href="#" style="margin-right:60px">ABOUT US</a>
    <a href="#" style="margin-right:58px">SERVICES</a>
    <a href="#" style="margin-right:58px">TESTIMONIALS</a>
    <a href="#" style="margin-right:58px">GALLERY</a>
    <a href="#">CONTACT US</a>
  </nav>
</header>

<section class="hero">
  <div class="photo" role="img" aria-label="Technician in hard hat turning a valve on industrial pipework at sunset" style="inset:0;background:linear-gradient(100deg,rgba(30,34,40,.85) 0%,rgba(60,55,50,.4) 45%,rgba(200,130,60,.2) 100%)"></div>
  <h1 class="heading"><span class="accent">KEELBROOK</span> MAINTENANCE</h1>
  <p>Lorem ipsum dolor sit amet, consectetur adipiscing elit, sed do incididunt ut labore et dolore magna aliqua.</p>
  <a class="btn" href="#" style="left:145px;top:335px;width:170px;height:42px">Get Started
    <svg width="12" height="12" viewBox="0 0 12 12"><path d="M1 6h9M6 2l4 4-4 4" stroke="#fff" stroke-width="2" fill="none"/></svg></a>
</section>

<section class="about">
  <h2 class="heading">ABOUT <span class="accent">US</span></h2>
  <div class="about-copy">
    <p>Director of the company has over 20-year experience in the fixed and mobile plant industries ranging from Perth local and overseas. Facilities like precious metals refining, offshore drilling and production platform, open cut and underground mining, civils, geotechnical and construction equipment and large-scale construction as an expat overseas.</p>
    <p>We offer personalised service to all small and medium size business across a diverse range of industries.</p>
  </div>
  <div class="stat" style="left:192px"><span class="stat-icon"></span><div><b>20</b><span>Years of Experiance</span></div></div>
  <div class="stat" style="left:482px"><span class="stat-icon"></span><div><b>10,000</b><span>Completed Projects</span></div></div>
  <div class="stat" style="left:773px"><span class="stat-icon"></span><div><b>1 Lakh</b><span>Happy Customers</span></div></div>
</section>
<div class="photo" role="img" aria-label="Welder in protective mask grinding metal with sparks in a workshop" style="left:145px;top:1140px;width:910px;height:430px;background:linear-gradient(110deg,#5c4a3a 0%,#8a6a48 35%,#d9a060 55%,#3f4a5c 80%,#2c3340 100%)"></div>

<h2 class="section-title heading" style="top:1685px"><span class="accent">OUR</span> SERVICES</h2>
<p class="lead" style="top:1805px">Lorem ipsum dolor sit amet, consectetur adipiscing elit, sed do eiusmod tempor incididunt ut labore et dolore magna aliqua. Ut enim ad minim veniam, quis nostrud exercitation ullamco commodo consequat.</p>

<article class="card" style="left:145px">
  <div class="photo" role="img" aria-label="Engineer in hard hat operating plant machinery" style="background:linear-gradient(120deg,#5a5a48,#9aa070 50%,#3e4650)"></div>
  <span class="icon-disc"></span>
  <h3>PLANT REPAIRS</h3>
  <p>Lorem ipsum dolor sit amet, consectetur adipiscing elit, sed do eiusmod</p>
  <div class="more">READ MORE ➜</div>
</article>
<article class="card featured" style="left:455px">
  <div class="photo" role="img" aria-label="Offshore drill rig platform at sea" style="background:linear-gradient(180deg,#7fa6c8 0%,#c89a60 55%,#3b5c7a 100%)"></div>
  <span class="icon-disc"></span>
  <h3>DRILL RIGS</h3>
  <p>Lorem ipsum dolor sit amet, consectetur adipiscing elit, sed do eiusmod</p>
  <div class="more">READ MORE ➜</div>
</article>
<article class="card" style="left:767px">
  <div class="photo" role="img" aria-label="Technician inspecting chemical processing pipework" style="background:linear-gradient(120deg,#1e4a6a,#4a8ab0 55%,#203a50)"></div>
  <span class="icon-disc"></span>
  <h3>CHEMICAL PROCESSING</h3>
  <p>Lorem ipsum dolor sit amet, consectetur adipiscing elit, sed do eiusmod</p>
  <div class="more">READ MORE ➜</div>
</article>
<div class="dot-grid"></div>
<a class="btn" href="#" style="left:500px;top:2345px;width:200px;height:42px">View All Services ➜</a>

<section class="projects">
  <h2 class="heading">LATEST PROJECTS</h2>
  <p class="lead-right">Lorem ipsum dolor sit amet, consectetur adipiscing elit, sed do eiusmod tempor incididunt ut labore et dolore magna aliqua.</p>
  <div class="photo" role="img" aria-label="Mechanic working on a large gear assembly" style="left:153px;top:213px;width:252px;height:150px;background:linear-gradient(120deg,#3a3e44,#8a6a40 60%,#2c3a4a)"></div>
  <div class="photo" role="img" aria-label="Worker servicing heavy machinery" style="left:417px;top:213px;width:270px;height:150px;background:linear-gradient(120deg,#2a3a4c,#c07a3a 55%,#2e3c4e)"></div>
  <div class="photo" role="img" aria-label="Technicians inspecting large pipelines" style="left:698px;top:213px;width:350px;height:150px;background:linear-gradient(120deg,#4a5a6a,#8a9aa8 50%,#3a4a5a)"></div>
  <div class="photo" role="img" aria-label="Engineer in hard hat checking valves in a plant" style="left:153px;top:375px;width:534px;height:238px;background:linear-gradient(120deg,#2c4a60,#d08a40 45%,#3a5a70)"></div>
  <div class="photo" role="img" aria-label="Machinist working on a metal shaft" style="left:698px;top:375px;width:350px;height:238px;background:linear-gradient(120deg,#3a4050,#8a7a6a 55%,#2a3040)"></div>
  <div class="pager"><i class="on"></i><i></i><i></i></div>
</section>

<h2 class="section-title heading" style="top:3295px"><span class="accent">LATEST</span> BLOG</h2>
<svg class="arrow" style="left:80px" viewBox="0 0 20 28"><path d="M15 3 5 14l10 11" stroke="#1f2a36" stroke-width="3" fill="none"/></svg>
<svg class="arrow" style="left:1100px" viewBox="0 0 20 28"><path d="M5 3l10 11L5 25" stroke="#1f2a36" stroke-width="3" fill="none"/></svg>
<article class="post" style="left:145px">
  <div class="photo" role="img" aria-label="Field engineer with tablet at an industrial site" style="background:linear-gradient(120deg,#5a4a3a,#c06a3a 55%,#2a3a4a)"></div>
  <h3>2021 Lorem ipsum dolor sit amet, consectetur adipiscing elit.</h3>
  <div class="date">Jun 24, 2020</div>
  <p>On June 24, 2020, sed do eiusmod tempor incididunt ut labore et.</p>
</article>
<article class="post" style="left:457px">
  <div class="photo" role="img" aria-label="Mechanic working on engine components" style="background:linear-gradient(120deg,#3a3e44,#7a6a5a 55%,#2a3038)"></div>
  <h3>2022 Lorem ipsum dolor sit amet, consectetur adipiscing elit.</h3>
  <div class="date" style="color:var(--blue)">Jun 24, 2020</div>
  <p>On June 24, 2020, sed do eiusmod tempor incididunt ut labore et.</p>
</article>
<article class="post" style="left:770px">
  <div class="photo" role="img" aria-label="Technician repairing a large orange gear housing" style="background:linear-gradient(120deg,#c0602a,#3a4a5a 55%,#d07a3a)"></div>
  <h3>2023 Lorem ipsum dolor sit amet, consectetur adipiscing elit.</h3>
  <div class="date">Jun 24, 2020</div>
  <p>On June 24, 2020, sed do eiusmod tempor incididunt ut labore et.</p>
</article>

<section class="contact">
  <h2 class="heading">CONTACT <span class="accent">US</span></h2>
  <div class="info" style="left:195px">
    <svg width="36" height="42" viewBox="0 0 24 28" fill="none" stroke="#fff" stroke-width="1.4"><path d="M12 26s-8-9-8-15a8 8 0 0 1 16 0c0 6-8 15-8 15z"/><circle cx="12" cy="11" r="3"/></svg>
    <div><b>LOCATION:</b><span>Lorem ipsum dolor sit amet,<br>consectetur 6514</span></div>
  </div>
  <div class="info" style="left:525px">
    <svg width="40" height="40" viewBox="0 0 24 24" fill="none" stroke="#fff" stroke-width="1.4"><path d="M5 3h4l2 5-3 2a12 12 0 0 0 6 6l2-3 5 2v4a2 2 0 0 1-2 2A17 17 0 0 1 3 5a2 2 0 0 1 2-2z"/></svg>
    <div><b>PHONE:</b><span>+61 8 5550 1472</span></div>
  </div>
  <div class="info" style="left:765px">
    <svg width="48" height="38" viewBox="0 0 30 22" fill="none" stroke="#fff" stroke-width="1.4"><rect x="1" y="1" width="28" height="20"/><path d="M1 1l14 11L29 1M1 21l10-9M29 21l-10-9"/></svg>
    <div><b>EMAIL:</b><span>info@keelbrookmaint.com</span></div>
  </div>
  <div class="field" style="top:305px">Name</div>
  <div class="field" style="top:367px">Email Address</div>
  <div class="field" style="top:427px">Phone Number</div>
  <div class="field message" style="top:303px">Message</div>
  <a class="btn" href="#" style="left:510px;top:510px;width:180px;height:44px">Submit Now ➜</a>
</section>

<footer class="site-footer">
  <div class="footer-brand"><span class="brand-dot"></span><span class="brand-name">Keelbrook<br>Maintenance</span></div>
  <div class="footer-follow">FOLLOW US: <span class="social"></span><span class="social"></span><span class="social"></span><span class="social"></span></div>
  <div class="col" style="left:448px"><h4>QUICK LINKS</h4><ul><li>Home</li><li>About Us</li><li>Services</li><li>Testimonials</li><li>Gallery</li><li>Contact Us</li></ul></div>
  <div class="col" style="left:668px"><h4>SERVICES</h4><ul><li>Our Company</li><li>Term of Services</li><li>Privacy Policy</li><li>Latest News</li><li>Site Map</li></ul></div>
  <div class="col" style="left:890px"><h4>CONTACT US</h4><ul>
    <li><span style="color:var(--blue-soft)">●</span>&nbsp; Lorem ipsum dolor sit amet.</li>
    <li><span style="color:var(--blue-soft)">●</span>&nbsp; +61 8 5550 1472</li>
    <li><span style="color:var(--blue-soft)">●</span>&nbsp; info@keelbrookmaint.com</li></ul></div>
  <div class="copyright">© Copyright 2024 / Keelbrook Maintenance / All Rights Reserved</div>
</footer>

</body>
</html>
```